Logistics Website Design

See website https://tqfreightglobal.com for theme and color details. Need the site to be re-done and reflect some of the designs shown in this list here: https://pixelvane.com/tags/logistics-company-website

Target Market(s)

Logistics & Transportation

Industry/Entity Type

Logistics and Supply Chain

Coding

Number of Pages Required

5+ page

Requirements
Must have
• Colors must match theme of logo. Looking for a sleek, interactive design.

```html
<!DOCTYPE html>
<html lang="en">
<head>
<meta charset="utf-8">
<title>TQ Freight Global — Logistics</title>
<link rel="stylesheet" href="https://fonts.googleapis.com/css2?family=Chakra+Petch:wght@700&family=Roboto:wght@400;500;700&display=swap">
<style>
:root{
  --orange:#e8602f;
  --orange-soft:#f6b59c;
  --ink:#111111;
  --black:#000000;
  --white:#ffffff;
  --text:#444444;
  --line:#cfcfcf;
}
*{box-sizing:border-box;margin:0;padding:0}
html,body{width:1200px;height:3556px;overflow:hidden;background:var(--white);font-family:"Roboto",sans-serif;color:var(--ink)}
.page{position:relative;width:1200px;height:3556px}
.abs{position:absolute}
.display{font-family:"Chakra Petch",sans-serif;font-weight:700;text-transform:uppercase;letter-spacing:1px}
.eyebrow{font-size:16px;color:var(--orange);text-transform:uppercase}
.bar{height:3px;background:var(--orange)}
.btn{display:flex;align-items:center;justify-content:center;background:var(--orange);color:var(--white);font-size:14px;font-weight:500;border-radius:5px;text-transform:uppercase}

/* header */
.site-header{left:0;top:0;width:1200px;height:72px;background:var(--black)}
.brand{left:150px;top:-8px;width:156px;height:156px;border-radius:50%;background:var(--black);border:5px solid var(--orange);display:flex;align-items:center;justify-content:center;text-align:center;color:var(--white);font-size:17px;font-weight:700;line-height:1.15}
.nav a{position:absolute;top:24px;color:var(--white);font-size:16px;font-weight:500;text-decoration:none}
.nav .active{color:var(--orange)}
.nav .active::after{content:"";position:absolute;left:0;right:0;top:40px;height:3px;background:var(--orange)}
.call-icon{left:846px;top:20px;width:34px;height:34px;border-radius:50%;background:var(--orange);display:flex;align-items:center;justify-content:center}
.call-text{left:890px;top:16px;color:var(--white);font-size:13px}
.call-text strong{display:block;font-size:19px;margin-top:2px}

/* hero */
.hero{left:0;top:72px;width:1200px;height:588px;background:linear-gradient(180deg,#b57a8c 0%,#6a5a78 30%,#3b3848 60%,#25242b 100%)}
.hero h1{left:600px;top:128px;width:460px;font-size:56px;line-height:64px;color:var(--white)}
.hero p{left:600px;top:316px;width:420px;font-size:19px;line-height:28px;font-weight:500;color:var(--white)}
.hero .btn{left:600px;top:379px;width:178px;height:40px}
.dots{left:566px;top:514px;display:flex;gap:6px}
.dots span{width:12px;height:12px;border-radius:50%;background:#cfcfcf}
.dots .on{background:var(--orange)}

/* about */
.about .eyebrow{left:144px;top:753px}
.about h2{left:144px;top:780px;font-size:46px}
.about .bar{left:144px;top:844px;width:118px}
.about p{left:144px;top:868px;width:431px;font-size:15.5px;line-height:22.5px;color:var(--text);text-align:justify}
.about .btn{left:144px;top:1131px;width:146px;height:40px}
.ring{border-radius:50%;border:3px solid var(--orange);background:#fde6dc;display:flex;align-items:center;justify-content:center}
.ring .photo{border-radius:50%}

/* services */
.services{left:0;top:1296px;width:1200px;height:625px;background:var(--black)}
.services .eyebrow{left:0;width:1200px;top:88px;text-align:center;color:var(--white)}
.services h2{left:0;width:1200px;top:110px;text-align:center;font-size:46px;color:var(--white)}
.services .bar{left:541px;top:172px;width:118px}
.card{top:209px;width:290px;height:300px;border:4px solid #cfcfcf;border-radius:14px;overflow:hidden}
.card-label{top:481px;width:222px;height:48px;font-size:16px;border-radius:6px;text-transform:uppercase}
.round-arrow{width:46px;height:46px;border-radius:50%;background:var(--white);display:flex;align-items:center;justify-content:center}

/* supply chain */
.supply{left:0;top:1921px;width:1200px;height:549px;background:var(--orange);overflow:hidden}
.supply h2{left:649px;top:88px;width:420px;font-size:48px;line-height:56px;color:var(--white)}
.supply .bar{left:649px;top:272px;width:118px;background:var(--white)}
.supply p{left:649px;top:292px;width:408px;font-size:15.5px;line-height:22.5px;color:var(--white);text-align:justify}

/* contact */
.contact .eyebrow{left:0;width:1200px;top:2576px;text-align:center}
.contact h2{left:0;width:1200px;top:2600px;text-align:center;font-size:46px}
.contact .bar{left:541px;top:2656px;width:118px}
.field{left:599px;width:458px;height:48px;border:1px solid var(--line);border-radius:6px;font-size:12px;color:#555;padding:17px 16px}
.contact .btn{left:599px;top:3039px;width:146px;height:40px}

/* footer */
.site-footer{left:0;top:3200px;width:1200px;height:356px;background:var(--black);color:var(--white)}
.col{top:70px}
.col h3{font-size:17px;font-weight:700;text-transform:uppercase}
.col .bar{width:48px;margin:10px 0 12px}
.col li{list-style:none;font-size:13px;line-height:20px}
.contact-line{display:flex;gap:12px;font-size:13px;line-height:20px;margin-bottom:20px}
.contact-line svg{flex:none;margin-top:3px}
.rule{left:143px;top:250px;width:914px;height:1px;background:#444}
.copy{left:0;width:1200px;top:277px;text-align:center;font-size:15px}
</style>
</head>
<body>
<div class="page">

  <!-- Header -->
  <header class="abs site-header">
    <nav class="nav">
      <a class="active" href="#" style="left:411px">Home</a>
      <a href="#" style="left:485px">About</a>
      <a href="#" style="left:561px">Services</a>
      <a href="#" style="left:654px">Industries</a>
      <a href="#" style="left:759px">Contact</a>
    </nav>
    <div class="abs call-icon">
      <svg width="16" height="16" viewBox="0 0 24 24"><path fill="#fff" d="M6.6 10.8a15.1 15.1 0 0 0 6.6 6.6l2.2-2.2c.3-.3.7-.4 1-.2 1.1.4 2.3.6 3.6.6.6 0 1 .4 1 1V20c0 .6-.4 1-1 1A17 17 0 0 1 3 4c0-.6.4-1 1-1h3.5c.6 0 1 .4 1 1 0 1.3.2 2.5.6 3.6.1.3 0 .7-.2 1z"/></svg>
    </div>
    <div class="abs call-text">Call Us Today :<strong>+1 888 888 8888</strong></div>
  </header>

  <!-- Hero -->
  <section class="abs hero" role="img" aria-label="Semi truck driving on a highway at dusk with mountains behind">
    <h1 class="abs display">Delivering strength in every mile</h1>
    <p class="abs">Secure and reliable transportation for all your cargo needs.</p>
    <a class="abs btn" href="#">Request a quote</a>
    <svg class="abs" style="left:56px;top:300px" width="32" height="48" viewBox="0 0 32 48"><path d="M26 4 6 24l20 20" fill="none" stroke="#fff" stroke-width="5"/></svg>
    <svg class="abs" style="left:1112px;top:300px" width="32" height="48" viewBox="0 0 32 48"><path d="M6 4l20 20L6 44" fill="none" stroke="#fff" stroke-width="5"/></svg>
    <div class="abs dots"><span></span><span class="on"></span><span></span><span></span></div>
  </section>

  <div class="abs brand">TQ Freight<br>Global</div>

  <!-- About -->
  <section class="about">
    <div class="abs eyebrow">About us</div>
    <h2 class="abs display">Who we are</h2>
    <div class="abs bar"></div>
    <p class="abs">TQ Freight Global™ was born out of real-world experience in the fitness equipment industry. What started as a company shipping strength equipment, cardio machines, and training gear to gyms, schools, and commercial facilities quickly evolved into something bigger. As order volume grew and supply chains became more complex, the team developed deep expertise in coordinating freight, managing deliveries, and navigating the challenges of large-scale equipment transportation. That hands-on experience laid the foundation for what would eventually become a full-service logistics operation.</p>
    <a class="abs btn" href="#">Learn more</a>
    <div class="abs ring" style="left:613px;top:736px;width:430px;height:430px">
      <div class="photo" role="img" aria-label="Red heavy haul truck carrying an oversize load on a lowboy trailer" style="width:396px;height:396px;background:linear-gradient(180deg,#dfe4ea 0%,#9aa4a0 45%,#8a4a3e 65%,#5b5d60 100%)"></div>
    </div>
  </section>

  <!-- Services -->
  <section class="abs services" role="region" aria-label="Our services">
    <div class="abs" role="img" aria-label="Faint dotted world map background" style="inset:0;background:radial-gradient(ellipse at 50% 45%,#1c1c1c 0%,#000 70%)"></div>
    <div class="abs eyebrow">Our services</div>
    <h2 class="abs display">What we do</h2>
    <div class="abs bar"></div>
    <div class="abs card" style="left:140px" role="img" aria-label="Truck on a rural road between green fields" ><div style="width:100%;height:100%;background:linear-gradient(180deg,#a9c4dd 0%,#d8e2e8 25%,#7fa356 45%,#5a7a3a 100%)"></div></div>
    <div class="abs card" style="left:456px" role="img" aria-label="Red step deck trailer parked by a warehouse"><div style="width:100%;height:100%;background:linear-gradient(180deg,#e8ecef 0%,#9aa6b0 35%,#c5392f 60%,#d2cbc4 100%)"></div></div>
    <div class="abs card" style="left:771px" role="img" aria-label="Dry van trailer on a highway at sunset"><div style="width:100%;height:100%;background:linear-gradient(180deg,#6c7486 0%,#b9a9ab 40%,#c59a86 65%,#2f2f36 100%)"></div></div>
    <div class="abs btn card-label" style="left:174px">Flatbed</div>
    <div class="abs btn card-label" style="left:489px">Step deck</div>
    <div class="abs btn card-label" style="left:804px">Dry van</div>
    <div class="abs round-arrow" style="left:50px;top:337px"><svg width="14" height="14" viewBox="0 0 14 14"><path d="M9 2 4 7l5 5" fill="none" stroke="#111" stroke-width="2"/></svg></div>
    <div class="abs round-arrow" style="left:1104px;top:337px"><svg width="14" height="14" viewBox="0 0 14 14"><path d="M5 2l5 5-5 5" fill="none" stroke="#111" stroke-width="2"/></svg></div>
  </section>

  <!-- Supply chain -->
  <section class="abs supply">
    <svg class="abs" style="left:0;top:0" width="600" height="549" viewBox="0 0 600 549" role="img" aria-label="Blue truck hauling a travel trailer on a flatbed past green trees">
      <defs>
        <linearGradient id="scene" x1="0" y1="0" x2="0" y2="1">
          <stop offset="0" stop-color="#b9d3ea"/>
          <stop offset="0.45" stop-color="#d5dbe0"/>
          <stop offset="0.62" stop-color="#3d5f9a"/>
          <stop offset="0.78" stop-color="#6f8f3e"/>
          <stop offset="1" stop-color="#5f7f35"/>
        </linearGradient>
      </defs>
      <path d="M0 0H440C620 180 620 380 460 549H0Z" fill="var(--orange-soft)"/>
      <path d="M0 0H425C600 180 600 380 445 549H0Z" fill="#fde6dc"/>
      <path d="M0 0H405C580 180 580 380 425 549H0Z" fill="url(#scene)"/>
    </svg>
    <h2 class="abs display">Keeping your supply chain moving</h2>
    <div class="abs bar"></div>
    <p class="abs">We deliver a comprehensive range of open-deck and specialized transportation services—including flatbed, step deck, heavy haul, and over-dimensional freight solutions. Backed by years of experience, a trusted nationwide carrier network, and a strong safety-first culture, we provide reliable, adaptable logistics support built around the unique requirements of every load.</p>
  </section>

  <!-- Contact -->
  <section class="contact">
    <div class="abs eyebrow">Contact</div>
    <h2 class="abs display">Get in touch</h2>
    <div class="abs bar"></div>
    <div class="abs ring" style="left:154px;top:2690px;width:406px;height:406px">
      <div class="photo" role="img" aria-label="Orange semi truck cab parked near city buildings" style="width:372px;height:372px;background:linear-gradient(90deg,#c7c9c6 0%,#9c9b94 35%,#e8621f 55%,#d4561b 75%,#8f8f8c 100%)"></div>
    </div>
    <div class="abs field" style="top:2695px">Name</div>
    <div class="abs field" style="top:2759px">Email address</div>
    <div class="abs field" style="top:2823px">Phone</div>
    <div class="abs field" style="top:2887px;height:136px">Message</div>
    <a class="abs btn" href="#">Submit now</a>
  </section>

  <!-- Footer -->
  <footer class="abs site-footer">
    <div class="abs col" style="left:143px">
      <h3>Quick links</h3><div class="bar"></div>
      <ul><li>Home</li><li>About us</li><li>Services</li><li>Industries</li><li>Contact</li></ul>
    </div>
    <div class="abs col" style="left:383px">
      <h3>Industries</h3><div class="bar"></div>
      <ul><li>Food &amp; Beverage</li><li>E-Commerce &amp; Retail</li><li>Manufacturing</li><li>Pharma &amp; Healthcare</li><li>Government</li></ul>
    </div>
    <div class="abs col" style="left:655px">
      <h3>Contact us</h3><div class="bar"></div>
      <div class="contact-line"><svg width="10" height="13" viewBox="0 0 10 13"><path d="M5 0a5 5 0 0 0-5 5c0 3.5 5 8 5 8s5-4.5 5-8a5 5 0 0 0-5-5zm0 7a2 2 0 1 1 0-4 2 2 0 0 1 0 4z" fill="var(--orange)"/></svg><span>Lorem ipsum dolor sit<br>amet, consectetur</span></div>
      <div class="contact-line"><svg width="12" height="12" viewBox="0 0 24 24"><path fill="var(--orange)" d="M6.6 10.8a15.1 15.1 0 0 0 6.6 6.6l2.2-2.2c.3-.3.7-.4 1-.2 1.1.4 2.3.6 3.6.6.6 0 1 .4 1 1V20c0 .6-.4 1-1 1A17 17 0 0 1 3 4c0-.6.4-1 1-1h3.5c.6 0 1 .4 1 1 0 1.3.2 2.5.6 3.6.1.3 0 .7-.2 1z"/></svg><span>+1 888 888 8888</span></div>
      <div class="contact-line"><svg width="12" height="10" viewBox="0 0 12 10"><rect width="12" height="10" rx="1" fill="var(--orange)"/><path d="M0 1l6 4 6-4" fill="none" stroke="#000" stroke-width="1"/></svg><span>info@companyname.com</span></div>
    </div>
    <div class="abs col" style="left:936px">
      <h3>Social media</h3><div class="bar"></div>
      <ul><li>Socialwall</li><li>Photoreel</li><li>Vidstream</li><li>Worknet</li></ul>
    </div>
    <div class="abs rule"></div>
    <div class="abs copy">© Copyrights 2026 Company name | All Rights reserved</div>
  </footer>

</div>
</body>
</html>
```